UK Online Auction Site needs a clever design

We need a contemporary landing page and registration page design for a UK auction website, that look equally at home on PC's and tablets . The design should be fresh, bright, clean, professional, robust, and familiar. We would like to see something clever but functional.

Online

```html
<!DOCTYPE html>
<html lang="en">
<head>
<meta charset="utf-8">
<title>Bidwell – Online Auctions</title>
<link href="https://fonts.googleapis.com/css2?family=Roboto+Condensed:wght@300;400;700&family=Open+Sans:wght@400;600;700&display=swap" rel="stylesheet">
<style>
:root{
  --blue:#1a8fd6;
  --blue-dark:#0f6fb3;
  --orange:#f7941d;
  --green:#7cc11f;
  --green-dark:#5e9e10;
  --pink:#f7c6e8;
  --text:#555;
  --heading:#1e8ed3;
  --footer:#222;
  --footer-text:#ddd;
  --card-band:rgba(20,20,20,.82);
}
*{box-sizing:border-box;margin:0;padding:0}
html,body{width:815px;height:1200px;overflow:hidden}
body{position:relative;background:#fbf9fb;font-family:"Open Sans",sans-serif;color:var(--text)}
.abs{position:absolute}
.brand{left:104px;top:18px;font-family:"Roboto Condensed",sans-serif;font-weight:700;font-size:32px;color:var(--blue);display:flex;align-items:center;gap:8px}
.brand .dot{width:14px;height:14px;border-radius:50%;background:var(--blue)}
.nav{top:30px;left:342px;display:flex;align-items:center;font-family:"Roboto Condensed",sans-serif;font-size:12px;color:#333;height:20px}
.nav a{display:flex;align-items:center;gap:4px;color:#333;text-decoration:none}
.nav .sell{position:absolute;left:0;width:56px;height:20px;border-radius:10px;background:var(--blue);color:#fff;justify-content:center}
.nav .signup{position:absolute;left:68px}
.nav .basket{position:absolute;left:133px}
.nav .help{position:absolute;left:198px}
.nav .contact{position:absolute;left:244px}
.nav .register{position:absolute;left:306px;width:64px;height:19px;border-radius:10px;background:var(--green);color:#fff;justify-content:center;font-size:11px}
.nav svg{width:9px;height:9px;fill:currentColor}
.searchbar{left:103px;top:74px;width:609px;height:34px;background:linear-gradient(#1b93dc,#0d75bf)}
.searchbar .field{position:absolute;top:4px;height:24px;background:#fff;display:flex;align-items:center;font-size:8px;color:#555}
.searchbar .cat{left:31px;width:130px;border-radius:12px 0 0 12px;padding-left:11px;justify-content:space-between;padding-right:9px;border-right:1px solid #ddd}
.searchbar .query{left:161px;width:304px;border-radius:0 12px 12px 0;padding-left:12px}
.searchbar .go{position:absolute;left:477px;top:4px;width:102px;height:25px;border-radius:13px;background:var(--orange);color:#fff;font-family:"Roboto Condensed",sans-serif;font-size:14px;display:flex;align-items:center;justify-content:center;gap:5px}
.hero{left:103px;top:120px;width:609px;height:162px;background:linear-gradient(90deg,#fde6f6,#f9cdef 55%,#f5b9e6)}
.hero .model{position:absolute;left:385px;top:0;width:136px;height:162px;background:linear-gradient(#3a2a30,#c89a8c 40%,#1d3b6a)}
.hero h2{position:absolute;left:51px;top:20px;font-family:"Roboto Condensed",sans-serif;font-weight:300;font-size:21px;color:#333}
.hero .offer{position:absolute;left:48px;top:40px;font-family:"Roboto Condensed",sans-serif;font-weight:300;font-size:42px;color:var(--blue)}
.hero .offer span{color:var(--orange)}
.hero .where{position:absolute;left:48px;top:89px;font-family:"Roboto Condensed",sans-serif;font-size:14px;color:#333}
.btn-green{background:linear-gradient(#8fd42b,var(--green-dark));color:#fff;display:flex;align-items:center;justify-content:center;gap:5px}
.hero .shop{position:absolute;left:48px;top:114px;width:99px;height:25px;border-radius:13px;font-family:"Roboto Condensed",sans-serif;font-size:13px}
.section-title{left:0;width:815px;text-align:center;font-family:"Roboto Condensed",sans-serif;font-weight:300;font-size:33px;color:var(--heading)}
.section-title b{font-weight:700}
.intro-photo{left:126px;top:378px;width:266px;height:147px;background:linear-gradient(90deg,#f2d2dc,#c99a88 45%,#3a2a26 80%,#f4c6de)}
.intro{left:418px;top:378px;width:266px}
.intro h3{font-family:"Roboto Condensed",sans-serif;font-weight:300;font-size:14.5px;color:var(--heading);margin-bottom:4px}
.intro p{font-size:8.6px;line-height:13px;color:#666}
.learn{left:418px;top:502px;width:86px;height:20px;border-radius:10px;font-size:8px}
.top-sub{left:0;top:606px;width:815px;text-align:center;font-size:9.6px;color:#444}
.card{width:144px;height:184px;overflow:hidden}
.card .band{position:absolute;left:0;bottom:0;width:100%;height:40px;background:var(--card-band);color:#fff;text-align:center;padding-top:7px}
.card .band h4{font-size:11px;font-weight:600}
.card .band small{display:block;font-size:7px;margin-top:2px}
.c1{left:103px}.c2{left:259px}.c3{left:414px}.c4{left:568px}
.r1{top:649px}.r2{top:846px}
.fashion{background:linear-gradient(#2c2624,#8a3a34 55%,#3a2a28)}
.garden{background:linear-gradient(#5f8f3c,#8d8f7a 45%,#c96a6a 75%,#5d7a3a)}
.collect{background:linear-gradient(90deg,#e8e6e2,#c9c3ba 50%,#f2f0ec)}
.jewel{background:linear-gradient(#f8e6f2,#b77a58 50%,#e9d4c0)}
.toy{background:linear-gradient(#d9c49a,#efe4d2 50%,#b89e78)}
.sport{background:linear-gradient(#5a6c86,#9c7e5e 50%,#243447)}
.motor{background:linear-gradient(#6a7078,#1f2226 55%,#0e0f10)}
.feature{background:linear-gradient(#1d98df,#0f78c4);color:#fff;text-align:center}
.feature .mark{margin-top:38px;font-family:"Open Sans",sans-serif;font-weight:700;font-size:22px}
.feature h4{margin-top:10px;font-size:11px;font-weight:700}
.feature p{margin:4px 10px 0;font-size:7px;line-height:10px}
.feature .outline{display:inline-block;margin-top:6px;border:1px solid #fff;padding:4px 9px;font-size:7px}
.footer{left:0;top:1066px;width:815px;height:134px;background:var(--footer);color:var(--footer-text)}
.footer h5{position:absolute;font-family:"Roboto Condensed",sans-serif;font-size:10px;font-weight:700;color:#fff}
.footer ul{position:absolute;list-style:none;font-size:7.5px;line-height:14.7px}
.social li{display:flex;align-items:center;gap:8px;height:16px;margin-bottom:5px}
.social i{display:block;width:16px;height:16px;border-radius:2px}
.foot-brand{position:absolute;left:600px;top:14px;width:112px;text-align:center;font-family:"Open Sans",sans-serif;font-weight:700;font-size:26px;color:#666}
.copy{position:absolute;right:103px;top:75px;width:130px;text-align:right;font-size:7.5px;line-height:10px}
</style>
</head>
<body>

<div class="abs brand"><span class="dot"></span>Bidwell</div>

<nav class="abs nav">
  <a class="sell" href="#"><svg viewBox="0 0 10 10"><path d="M0 1v4l5 5 5-5-5-5H1zM2.5 2.5a1 1 0 1 1 0 .1z"/></svg>Sell ▾</a>
  <a class="signup" href="#"><svg viewBox="0 0 10 10"><circle cx="5" cy="3" r="2.5"/><path d="M0 10c0-3 2-4.5 5-4.5s5 1.5 5 4.5z"/></svg>Sign Up ▾</a>
  <a class="basket" href="#"><svg viewBox="0 0 10 10"><path d="M0 4h10l-1.5 5h-7zM3 4l2-3 2 3z"/></svg>Basket ▾</a>
  <a class="help" href="#"><svg viewBox="0 0 10 10"><circle cx="5" cy="5" r="5"/></svg>Help</a>
  <a class="contact" href="#"><svg viewBox="0 0 10 10"><path d="M0 2h10v6H0z"/></svg>Contact</a>
  <a class="register" href="#"><svg viewBox="0 0 10 10"><circle cx="5" cy="3" r="2.5"/><path d="M0 10c0-3 2-4.5 5-4.5s5 1.5 5 4.5z"/></svg>Register</a>
</nav>

<form class="abs searchbar">
  <div class="field cat">All Categories <span>▾</span></div>
  <div class="field query">Search for a brand,product or specific item</div>
  <div class="go"><svg width="11" height="11" viewBox="0 0 12 12"><circle cx="5" cy="5" r="3.6" fill="none" stroke="#fff" stroke-width="1.8"/><path d="M7.6 7.6l3.4 3.4" stroke="#fff" stroke-width="2"/></svg>Search</div>
</form>

<section class="abs hero">
  <h2>JEWELLERY &amp; BEAUTY</h2>
  <div class="offer"><span>25%</span> OFF</div>
  <div class="where">ONLINE &amp; IN STORE</div>
  <a class="shop btn-green" href="#"><svg width="10" height="10" viewBox="0 0 10 10"><path fill="#fff" d="M0 4h10l-1.5 5h-7zM3 4l2-3 2 3z"/></svg>Shop Now</a>
  <div class="model" role="img" aria-label="Photo of a model wearing a necklace and earrings"></div>
</section>

<h1 class="abs section-title" style="top:314px"><b>Hi There</b> Nice to meet you</h1>

<div class="abs intro-photo" role="img" aria-label="Photo of three women with styled hair"></div>
<div class="abs intro">
  <h3>Lets talk about Bidwells</h3>
  <p>It is a long established fact that a reader will be distracted by the readable content of a page when looking at its layout. The point of using Lorem Ipsum is that it has a more-or-less normal distri-bution of letters, as opposed to using 'Content here, content here', making it look like readable English. Many desktop pub-lishing packages and web page editors now use Lorem Ipsum as their default model text.</p>
</div>
<a class="abs learn btn-green" href="#">Learn More ⟶</a>

<h2 class="abs section-title" style="top:562px"><b>Top</b> Products</h2>
<p class="abs top-sub">It is a long established fact that a reader will be distracted by the readable content.</p>

<div class="abs card c1 r1 fashion" role="img" aria-label="Fashion photo of a model in a scarf and sunglasses"><div class="band"><h4>Fashion</h4><small>See All Product →</small></div></div>
<div class="abs card c2 r1 garden" role="img" aria-label="Photo of a house with a front garden"><div class="band"><h4>Home &amp; Garden</h4><small>See All Product →</small></div></div>
<div class="abs card c3 r1 feature">
  <div class="mark">Bidwell</div>
  <h4>Electricals &amp; Technology</h4>
  <p>It is a long established fact that a reader will be distracted by the reada-ble content</p>
  <span class="outline">See All Product →</span>
</div>
<div class="abs card c4 r1 collect" role="img" aria-label="Photo of a vintage bathroom interior"><div class="band"><h4>Collectables &amp; Aniques</h4><small>See All Product →</small></div></div>

<div class="abs card c1 r2 jewel" role="img" aria-label="Photo of a woman wearing traditional gold jewellery"><div class="band"><h4>Jewellery &amp; Beauty</h4><small>See All Product →</small></div></div>
<div class="abs card c2 r2 toy" role="img" aria-label="Photo of a teddy bear"><div class="band"><h4>Toy</h4><small>See All Product →</small></div></div>
<div class="abs card c3 r2 sport" role="img" aria-label="Photo of a bowling ball and pins"><div class="band"><h4>Sport &amp; Leisure</h4><small>See All Product →</small></div></div>
<div class="abs card c4 r2 motor" role="img" aria-label="Photo of a sports motorbike"><div class="band"><h4>Motors</h4><small>See All Product →</small></div></div>

<footer class="abs footer">
  <h5 style="left:104px;top:27px">Site Map</h5>
  <ul style="left:104px;top:41px"><li>Contact</li><li>Terms</li><li>Privacy</li><li>RSS</li></ul>
  <ul style="left:164px;top:41px"><li>About</li><li>News</li><li>Feeds</li></ul>
  <h5 style="left:253px;top:27px">Buy</h5>
  <ul style="left:253px;top:44px"><li>Categories</li><li>Search</li><li>Currency</li><li>Converter</li></ul>
  <h5 style="left:353px;top:27px">Sell</h5>
  <ul style="left:353px;top:44px"><li>Sell New Item</li><li>Sell Bulk Items</li></ul>
  <h5 style="left:474px;top:23px">Follow Us</h5>
  <ul class="social" style="left:475px;top:39px;line-height:16px">
    <li><i style="background:#3b5a9a"></i>Friendlink</li>
    <li><i style="background:#2fa9e0"></i>Chirpline</li>
    <li><i style="background:#d3402f"></i>Circlespace</li>
  </ul>
  <div class="foot-brand">Bidwell</div>
  <p class="copy">Copyright Bidwell ® 2003-13. All rights reserved</p>
</footer>

</body>
</html>
```